Business Card Design

We are a commercial real estate brokerage in San Francisco, leasing office buildings downtown.
I would like a clean, elegant look. Simple but powerful .

Industry/Entity Type

Business

Contact Information for Business Card

Derek Holloway
lic# 07258143
415.555.0172
derek@velt-commercial.example
velt-commercial.example

```html
<!DOCTYPE html>
<html lang="en">
<head>
<meta charset="utf-8">
<title>Velt Commercial — Business Card</title>
<link rel="stylesheet" href="https://fonts.googleapis.com/css2?family=Source+Sans+3:wght@400;600&display=swap">
<style>
  :root {
    --page-bg: #8e9093;
    --card-bg: #edeef0;
    --brand-blue: #5b6b8c;
    --ink-dark: #4a4a4c;
    --ink-soft: #505256;
    --skyline-dark: #a9abaf;
    --skyline-light: #dcdde0;
  }
  * { margin: 0; padding: 0; box-sizing: border-box; }
  html, body {
    width: 1105px;
    height: 1200px;
    overflow: hidden;
    background: var(--page-bg);
    font-family: "Source Sans 3", "Helvetica Neue", Arial, sans-serif;
  }
  .canvas {
    position: relative;
    width: 1105px;
    height: 1200px;
  }
  .card {
    position: absolute;
    left: 180px;
    width: 746px;
    height: 427px;
    background: var(--card-bg);
    overflow: hidden;
  }
  .card-front { top: 119px; }
  .card-back { top: 636px; }

  .skyline-area {
    position: absolute;
    left: 0;
    top: 0;
    width: 620px;
    height: 100%;
    background: linear-gradient(90deg, var(--skyline-dark) 0%, #bfc1c4 45%, var(--skyline-light) 80%, rgba(237,238,240,0) 100%);
    opacity: 0.75;
  }

  .front-details {
    position: absolute;
    right: 56px;
    top: 58px;
    text-align: right;
  }
  .wordmark-name {
    display: block;
    color: var(--brand-blue);
    font-weight: 600;
    line-height: 1;
  }
  .wordmark-front .wordmark-top { font-size: 84px; letter-spacing: 1px; }
  .wordmark-front .wordmark-bottom { font-size: 36px; margin-top: 4px; letter-spacing: 0.5px; }

  .agent-name {
    margin-top: 30px;
    font-size: 25px;
    font-weight: 600;
    color: var(--brand-blue);
    letter-spacing: 0.5px;
  }
  .licence {
    margin-top: 14px;
    font-size: 19px;
    color: var(--ink-soft);
  }
  .contact-list {
    list-style: none;
    margin-top: 14px;
  }
  .contact-item {
    display: flex;
    justify-content: flex-end;
    align-items: center;
    gap: 12px;
    font-size: 19px;
    color: var(--ink-soft);
    height: 29px;
  }
  .contact-icon {
    width: 18px;
    height: 18px;
    flex: none;
  }

  .back-logo {
    position: absolute;
    left: 0;
    right: 0;
    top: 170px;
    text-align: center;
  }
  .wordmark-back .wordmark-top { font-size: 66px; letter-spacing: 1px; }
  .wordmark-back .wordmark-bottom { font-size: 30px; margin-top: 4px; letter-spacing: 0.5px; }
</style>
</head>
<body>
<main class="canvas">

  <section class="card card-front">
    <div class="skyline-area" role="img" aria-label="Faint illustration of downtown office towers"></div>

    <div class="front-details">
      <div class="wordmark wordmark-front">
        <span class="wordmark-name wordmark-top">VELT</span>
        <span class="wordmark-name wordmark-bottom">COMMERCIAL</span>
      </div>
      <p class="agent-name">DEREK HOLLOWAY</p>
      <p class="licence">lic# 07258143</p>
      <ul class="contact-list">
        <li class="contact-item">
          <span>415.555.0172</span>
          <svg class="contact-icon" viewBox="0 0 24 24" aria-hidden="true">
            <path fill="var(--brand-blue)" d="M6.6 10.8c1.4 2.8 3.8 5.1 6.6 6.6l2.2-2.2c.3-.3.7-.4 1-.2 1.1.4 2.3.6 3.6.6.6 0 1 .4 1 1V20c0 .6-.4 1-1 1C10.6 21 3 13.4 3 4c0-.6.4-1 1-1h3.5c.6 0 1 .4 1 1 0 1.3.2 2.5.6 3.6.1.3 0 .7-.2 1l-2.3 2.2z"/>
          </svg>
        </li>
        <li class="contact-item">
          <span>derek@velt-commercial.example</span>
          <svg class="contact-icon" viewBox="0 0 24 24" aria-hidden="true">
            <rect x="2" y="5" width="20" height="14" rx="1.5" fill="var(--brand-blue)"/>
            <path d="M3 6.5l9 6.5 9-6.5" fill="none" stroke="var(--card-bg)" stroke-width="1.6"/>
          </svg>
        </li>
        <li class="contact-item">
          <span>velt-commercial.example</span>
          <svg class="contact-icon" viewBox="0 0 24 24" aria-hidden="true">
            <circle cx="12" cy="12" r="10" fill="var(--brand-blue)"/>
            <g fill="none" stroke="var(--card-bg)" stroke-width="1.3">
              <ellipse cx="12" cy="12" rx="4" ry="9"/>
              <path d="M3 12h18M5 7.5h14M5 16.5h14"/>
            </g>
          </svg>
        </li>
      </ul>
    </div>
  </section>

  <section class="card card-back">
    <div class="back-logo">
      <div class="wordmark wordmark-back">
        <span class="wordmark-name wordmark-top">VELT</span>
        <span class="wordmark-name wordmark-bottom">COMMERCIAL</span>
      </div>
    </div>
  </section>

</main>
</body>
</html>
```